UX Design for Analytics Web Application

http://velqoranthe.com/
We are tech & consulting company with analytics products (web applications), located at Rio de Janeiro, Brazil.

We are searching a partner do develop UX for our products, i.e, aesthetics, usability, HTML/CSS.

Currently we have a product suite and the goal is to make a pilot re-design project with one of our products.

The product of interest is interactive webapp that aims at data analysis, significantly different from blogs, e-commerce or landing pages.

We do have a software development team but we lack an UX & HTML expert. Currently we use Bootstrap templates but the results are insatisfatory.

So, the project scope is, to develop the arts (UX, aesthetics, etc) along with the code/mockup (HTML/CSS) for one of our product (3 pages).

This is a pilot project and there's potential to rehire for our other products. Code quality is of importance.

More details and specification can be found in attached files.

Target Market(s)

Executives, managers & consultants

Industry/Entity Type

It Company

Coding

Coded - Design and coding required

Number of Pages Required

3 page

Font styles to use
Sans Serif

Requirements
Must have
• (see attached files, prefer the pptx version))
• -Responsive
Nice to have
• (see attached files, prefer the pptx version)
Should not have
• -Avoid Green, Red and Yellow colors. They have a meaning of good, bad and average in our products.

```html
<!DOCTYPE html>
<html lang="en">
<head>
<meta charset="utf-8">
<title>Visitors Overview · Analytics Dashboard</title>
<link href="https://fonts.googleapis.com/css2?family=Rubik:wght@400;500&display=swap" rel="stylesheet">
<style>
:root{
  --page-bg:#f0f0f2;
  --card-bg:#ffffff;
  --ink:#1f2023;
  --ink-soft:#4a4c52;
  --ink-muted:#6c6f76;
  --line:#e6e6ea;
  --purple:#9575cd;
  --purple-deep:#7e57c2;
  --purple-fill:rgba(149,117,205,.16);
  --blue:#2f8fdc;
  --blue-fill:rgba(47,143,220,.10);
  --indigo:#3f51b5;
  --indigo-fill:rgba(63,81,181,.08);
  --cyan:#29b6d6;
  --slate:#5f6b7a;
  --rise:#1e7fd0;
  --fall:#7e57c2;
  --badge-primary:#8e6bd0;
  --badge-blue:#29a8e0;
}
*{box-sizing:border-box;margin:0;padding:0}
html,body{width:1200px;height:689px;overflow:hidden}
body{background:var(--page-bg);font-family:"Rubik",Arial,sans-serif;color:var(--ink);position:relative}

/* top bar */
.topbar{position:absolute;left:0;top:0;width:1200px;height:53px;background:var(--card-bg);box-shadow:0 1px 4px rgba(0,0,0,.08)}
.topbar svg{position:absolute}
.topbar .mega{position:absolute;left:396px;top:17px;font-size:13.5px;color:var(--ink-soft)}
.topbar .lang{position:absolute;left:894px;top:17px;font-size:13.5px;color:var(--ink-soft)}
.badge{position:absolute;width:19px;height:19px;border-radius:50%;color:#fff;font-size:10.5px;line-height:19px;text-align:center}
.badge.primary{background:var(--badge-primary)}
.badge.blue{background:var(--badge-blue)}
.avatar{position:absolute;left:1073px;top:12px;width:28px;height:28px;border-radius:50%;background:linear-gradient(135deg,#c9b8a6,#6f6a66)}
.avatar-dot{position:absolute;left:1093px;top:33px;width:8px;height:8px;border-radius:50%;background:var(--blue);border:1.5px solid #fff}
.user{position:absolute;left:1109px;top:19px;font-size:13.5px;color:var(--ink-soft)}

/* sidebar */
.sidebar{position:absolute;left:24px;top:76px;width:224px;height:640px;background:var(--card-bg);box-shadow:0 1px 3px rgba(0,0,0,.05)}
.search{position:absolute;left:19px;top:17px;width:186px;height:32px;border:1px solid #cfd0d4;border-radius:16px;font-size:13px;color:#8a8c92;padding:8px 13px}
.nav-item{position:absolute;left:0;width:224px;height:24px;font-size:13.5px;color:var(--ink)}
.nav-item .icon{position:absolute;left:19px;top:4px}
.nav-item .label{position:absolute;left:45px;top:3px}
.nav-item .chev{position:absolute;left:196px;top:6px}
.nav-heading{position:absolute;left:19px;font-size:13px;color:var(--ink);letter-spacing:.3px}

/* cards */
.card{position:absolute;background:var(--card-bg);box-shadow:0 1px 3px rgba(0,0,0,.05)}
.overview{left:276px;top:76px;width:899px;height:547px}
.card-title{position:absolute;left:20px;top:15px;font-size:17px;font-weight:500;color:var(--ink)}
.range{position:absolute;left:695px;top:13px;height:31px;display:flex;border:1px solid var(--purple);border-radius:16px;overflow:hidden}
.range span{font-size:13px;color:var(--purple);padding:7px 13px;border-left:1px solid var(--purple)}
.range span:first-child{border-left:none;background:var(--purple);color:#fff;padding:7px 14px}
.stat{position:absolute;top:90px;width:200px;text-align:center}
.stat .value{font-size:21px;color:var(--ink)}
.stat .caption{margin-top:8px;font-size:13px;color:var(--ink-muted)}
.stat .up{color:var(--rise)}
.stat .down{color:var(--fall)}
.stat svg{display:block;margin:10px auto 0}
.divider{position:absolute;top:77px;width:1px;height:107px;background:var(--line)}
.legend{position:absolute;top:234px;left:0;width:899px;text-align:center;font-size:13px;color:var(--ink)}
.legend i{display:inline-block;width:11px;height:11px;border-radius:50%;vertical-align:-1px;margin:0 4px 0 10px}
.chart{position:absolute;left:0;top:254px}
.chart text{font-family:"Rubik",Arial,sans-serif;font-size:11px;fill:var(--ink-soft)}

.share{left:276px;top:651px;width:279px;height:80px}
.share .big{position:absolute;left:20px;top:22px;font-size:40px;color:var(--ink)}
.platforms{left:587px;top:651px;width:588px;height:80px}
.platforms .legend{top:20px;width:588px;left:0}
</style>
</head>
<body>

<header class="topbar">
  <svg style="left:253px;top:18px" width="20" height="16" viewBox="0 0 20 16"><g stroke="#333" stroke-width="2"><line x1="1" y1="2" x2="19" y2="2"/><line x1="1" y1="8" x2="19" y2="8"/><line x1="1" y1="14" x2="19" y2="14"/></g></svg>
  <svg style="left:303px;top:17px" width="17" height="17" viewBox="0 0 17 17"><circle cx="7" cy="7" r="5.5" fill="none" stroke="#333" stroke-width="1.8"/><line x1="11" y1="11" x2="16" y2="16" stroke="#333" stroke-width="1.8"/></svg>
  <svg style="left:352px;top:17px" width="17" height="17" viewBox="0 0 17 17"><path d="M1 6V1h5M11 1h5v5M16 11v5h-5M6 16H1v-5" fill="none" stroke="#333" stroke-width="1.6"/></svg>
  <span class="mega">Mega ⌄</span>
  <svg style="left:869px;top:20px" width="19" height="13" viewBox="0 0 19 13"><rect width="19" height="13" fill="#fff"/><g fill="#c8312e"><rect y="0" width="19" height="1.9"/><rect y="3.7" width="19" height="1.9"/><rect y="7.4" width="19" height="1.9"/><rect y="11.1" width="19" height="1.9"/></g><rect width="8.5" height="7" fill="#2f3d7a"/></svg>
  <span class="lang">English ⌄</span>
  <svg style="left:966px;top:17px" width="17" height="18" viewBox="0 0 17 18"><path d="M3 13V8a5.5 5.5 0 0 1 11 0v5l1.5 2h-14z" fill="none" stroke="#333" stroke-width="1.6"/><path d="M6.5 16.5a2 2 0 0 0 4 0" fill="none" stroke="#333" stroke-width="1.4"/></svg>
  <span class="badge primary" style="left:977px;top:8px">5</span>
  <svg style="left:1020px;top:19px" width="18" height="14" viewBox="0 0 18 14"><rect x="1" y="1" width="16" height="12" fill="none" stroke="#333" stroke-width="1.6"/><path d="M1 1l8 6 8-6" fill="none" stroke="#333" stroke-width="1.6"/></svg>
  <span class="badge blue" style="left:1030px;top:8px">8</span>
  <div class="avatar" role="img" aria-label="User profile photo"></div>
  <span class="avatar-dot"></span>
  <span class="user">John Doe ⌄</span>
</header>

<nav class="sidebar">
  <div class="search">Search</div>

  <div class="nav-item" style="top:76px"><svg class="icon" width="16" height="15" viewBox="0 0 16 15"><path d="M1 8L8 1l7 7M3 7v7h4v-4h2v4h4V7" fill="#333"/></svg><span class="label">Dashboard</span><svg class="chev" width="7" height="11" viewBox="0 0 7 11"><path d="M1 1l4.5 4.5L1 10" fill="none" stroke="#333" stroke-width="1.5"/></svg></div>
  <div class="nav-item" style="top:115px"><svg class="icon" width="16" height="15" viewBox="0 0 16 15"><rect x="1" y="1" width="14" height="13" fill="none" stroke="#333" stroke-width="1.4"/><line x1="1" y1="5" x2="15" y2="5" stroke="#333" stroke-width="1.4"/><rect x="3" y="7" width="4" height="5" fill="#333"/></svg><span class="label">Templates</span><svg class="chev" width="7" height="11" viewBox="0 0 7 11"><path d="M1 1l4.5 4.5L1 10" fill="none" stroke="#333" stroke-width="1.5"/></svg></div>
  <div class="nav-heading" style="top:157px">LAYOUTS</div>
  <div class="nav-item" style="top:192px"><svg class="icon" width="16" height="15" viewBox="0 0 16 15"><rect x="4" y="1" width="11" height="10" fill="none" stroke="#333" stroke-width="1.4"/><path d="M1 4v10h11" fill="none" stroke="#333" stroke-width="1.4"/></svg><span class="label">Page layouts</span><svg class="chev" width="7" height="11" viewBox="0 0 7 11"><path d="M1 1l4.5 4.5L1 10" fill="none" stroke="#333" stroke-width="1.5"/></svg></div>
  <div class="nav-item" style="top:230px"><svg class="icon" width="16" height="15" viewBox="0 0 16 15"><g stroke="#333" stroke-width="2"><line x1="1" y1="3" x2="15" y2="3"/><line x1="1" y1="8" x2="15" y2="8"/><line x1="1" y1="13" x2="15" y2="13"/></g></svg><span class="label">Navbars</span><svg class="chev" width="7" height="11" viewBox="0 0 7 11"><path d="M1 1l4.5 4.5L1 10" fill="none" stroke="#333" stroke-width="1.5"/></svg></div>
  <div class="nav-item" style="top:269px"><svg class="icon" width="16" height="15" viewBox="0 0 16 15"><path d="M3 1h10M3 14h10M5 1v13M11 1v13" fill="none" stroke="#333" stroke-width="1.4"/></svg><span class="label">Vertical Nav</span><svg class="chev" width="7" height="11" viewBox="0 0 7 11"><path d="M1 1l4.5 4.5L1 10" fill="none" stroke="#333" stroke-width="1.5"/></svg></div>
  <div class="nav-item" style="top:307px"><svg class="icon" width="16" height="15" viewBox="0 0 16 15"><path d="M1 3v9M15 3v9M1 5h14M1 10h14" fill="none" stroke="#333" stroke-width="1.4"/></svg><span class="label">Horizontal Nav</span><svg class="chev" width="7" height="11" viewBox="0 0 7 11"><path d="M1 1l4.5 4.5L1 10" fill="none" stroke="#333" stroke-width="1.5"/></svg></div>
  <div class="nav-item" style="top:346px"><svg class="icon" width="16" height="15" viewBox="0 0 16 15"><path d="M1 3v9M15 3v9M1 5h14M1 10h14" fill="none" stroke="#333" stroke-width="1.4"/></svg><span class="label">Page Headers</span><svg class="chev" width="7" height="11" viewBox="0 0 7 11"><path d="M1 1l4.5 4.5L1 10" fill="none" stroke="#333" stroke-width="1.5"/></svg></div>
  <div class="nav-item" style="top:384px"><svg class="icon" width="16" height="15" viewBox="0 0 16 15"><path d="M8 1v9M5 7l3 3 3-3M3 14h10" fill="none" stroke="#333" stroke-width="1.4"/></svg><span class="label">Footers</span><svg class="chev" width="7" height="11" viewBox="0 0 7 11"><path d="M1 1l4.5 4.5L1 10" fill="none" stroke="#333" stroke-width="1.5"/></svg></div>
  <div class="nav-heading" style="top:427px">GENERAL</div>
  <div class="nav-item" style="top:461px"><svg class="icon" width="16" height="15" viewBox="0 0 16 15"><rect x="1" y="1" width="12" height="5" fill="#333"/><path d="M13 3.5h2v4H8v2" fill="none" stroke="#333" stroke-width="1.4"/><rect x="6.5" y="9.5" width="3" height="5" fill="#333"/></svg><span class="label">Color Palette</span><svg class="chev" width="7" height="11" viewBox="0 0 7 11"><path d="M1 1l4.5 4.5L1 10" fill="none" stroke="#333" stroke-width="1.5"/></svg></div>
  <div class="nav-item" style="top:500px"><svg class="icon" width="16" height="15" viewBox="0 0 16 15"><path d="M8 1a4.5 4.5 0 0 0-2.5 8.2V11h5V9.2A4.5 4.5 0 0 0 8 1zM6 13h4" fill="none" stroke="#333" stroke-width="1.4"/></svg><span class="label">Starter kit</span><svg class="chev" width="7" height="11" viewBox="0 0 7 11"><path d="M1 1l4.5 4.5L1 10" fill="none" stroke="#333" stroke-width="1.5"/></svg></div>
  <div class="nav-item" style="top:538px"><svg class="icon" width="16" height="15" viewBox="0 0 16 15"><rect x="1" y="1" width="9" height="9" fill="none" stroke="#333" stroke-width="1.4"/><rect x="6" y="5" width="9" height="9" fill="#fff" stroke="#333" stroke-width="1.4"/></svg><span class="label">Changelog</span></div>
  <div class="nav-item" style="top:577px"><svg class="icon" width="16" height="15" viewBox="0 0 16 15"><path d="M1 7.5C3 4 5.5 3 8 3s5 1 7 4.5C13 11 10.5 12 8 12s-5-1-7-4.5z" fill="none" stroke="#333" stroke-width="1.4"/><circle cx="8" cy="7.5" r="2" fill="#333"/><line x1="2" y1="13" x2="14" y2="2" stroke="#333" stroke-width="1.4"/></svg><span class="label">Disabled Menu</span></div>
</nav>

<section class="card overview">
  <h2 class="card-title">Visitors Overview</h2>
  <div class="range"><span>Hourly</span><span>Day</span><span>Month</span></div>

  <div class="stat" style="left:55px">
    <div class="value">15,678</div>
    <div class="caption">Total Visit <span class="up">↑ 4.27%</span></div>
    <svg width="146" height="30" viewBox="0 0 146 30"><g fill="var(--purple)">
      <rect x="0" y="28" width="2.4" height="2"/><rect x="5.2" y="27" width="2.4" height="3"/><rect x="10.4" y="25" width="2.4" height="5"/><rect x="15.6" y="23" width="2.4" height="7"/><rect x="20.8" y="20" width="2.4" height="10"/><rect x="26" y="17" width="2.4" height="13"/><rect x="31.2" y="13" width="2.4" height="17"/><rect x="36.4" y="9" width="2.4" height="21"/><rect x="41.6" y="12" width="2.4" height="18"/><rect x="46.8" y="14" width="2.4" height="16"/><rect x="52" y="17" width="2.4" height="13"/><rect x="57.2" y="19" width="2.4" height="11"/><rect x="62.4" y="22" width="2.4" height="8"/><rect x="67.6" y="24" width="2.4" height="6"/><rect x="72.8" y="25" width="2.4" height="5"/><rect x="78" y="21" width="2.4" height="9"/><rect x="83.2" y="17" width="2.4" height="13"/><rect x="88.4" y="12" width="2.4" height="18"/><rect x="93.6" y="7" width="2.4" height="23"/><rect x="98.8" y="4" width="2.4" height="26"/><rect x="104" y="6" width="2.4" height="24"/><rect x="109.2" y="11" width="2.4" height="19"/><rect x="114.4" y="15" width="2.4" height="15"/><rect x="119.6" y="18" width="2.4" height="12"/><rect x="124.8" y="21" width="2.4" height="9"/><rect x="130" y="24" width="2.4" height="6"/><rect x="135.2" y="26" width="2.4" height="4"/>
    </g></svg>
  </div>
  <div class="divider" style="left:300px"></div>

  <div class="stat" style="left:349px">
    <div class="value">8,630</div>
    <div class="caption">Unique Visitor <span class="down">↓ 2.30%</span></div>
    <svg width="118" height="30" viewBox="0 0 118 30">
      <g fill="var(--indigo)"><rect x="0" y="19" width="4" height="11"/><rect x="18" y="16" width="4" height="14"/><rect x="36" y="15" width="4" height="15"/><rect x="54" y="19" width="4" height="11"/><rect x="72" y="21" width="4" height="9"/><rect x="90" y="13" width="4" height="17"/><rect x="108" y="14" width="4" height="16"/></g>
      <g fill="var(--cyan)"><rect x="9" y="14" width="4" height="16"/><rect x="27" y="9" width="4" height="21"/><rect x="45" y="13" width="4" height="17"/><rect x="63" y="14" width="4" height="16"/><rect x="81" y="3" width="4" height="27"/><rect x="99" y="11" width="4" height="19"/></g>
    </svg>
  </div>
  <div class="divider" style="left:597px"></div>

  <div class="stat" style="left:644px">
    <div class="value">32,454</div>
    <div class="caption">Page Views <span class="up">↑ 8.16%</span></div>
    <svg width="132" height="30" viewBox="0 0 132 30">
      <g fill="var(--cyan)"><rect x="0" y="3" width="3" height="10"/><rect x="13" y="3" width="3" height="6"/><rect x="26" y="3" width="3" height="12"/><rect x="65" y="3" width="3" height="8"/><rect x="91" y="3" width="3" height="10"/><rect x="104" y="3" width="3" height="6"/><rect x="117" y="3" width="3" height="11"/></g>
      <g fill="var(--purple-deep)"><rect x="39" y="15" width="3" height="13"/><rect x="52" y="15" width="3" height="8"/><rect x="78" y="15" width="3" height="10"/><rect x="128" y="15" width="3" height="13"/></g>
    </svg>
  </div>

  <div class="legend"><i style="background:var(--purple)"></i>Page Views <i style="background:var(--blue)"></i>Total Visit <i style="background:var(--indigo)"></i>Unique Visitor</div>

  <svg class="chart" width="899" height="290" viewBox="0 0 899 290" role="img" aria-label="Line chart of page views, total visits and unique visitors over the last 25 seconds">
    <g stroke="#e8e8ec" stroke-width="1">
      <line x1="69" y1="22" x2="861" y2="22"/><line x1="69" y1="54" x2="861" y2="54"/><line x1="69" y1="119" x2="861" y2="119"/><line x1="69" y1="183" x2="861" y2="183"/><line x1="69" y1="247" x2="861" y2="247"/><line x1="69" y1="22" x2="69" y2="247"/>
    </g>
    <g text-anchor="end"><text x="60" y="26">35000</text><text x="60" y="58">30000</text><text x="60" y="123">20000</text><text x="60" y="187">10000</text><text x="60" y="251">0</text></g>
    <g text-anchor="middle"><text x="69" y="267">-25 Sec</text><text x="227" y="267">-20 Sec</text><text x="387" y="267">-15 Sec</text><text x="544" y="267">-10 Sec</text><text x="703" y="267">-5 Sec</text><text x="861" y="267">0 Sec</text></g>

    <path d="M69 26C122 26 174 110 227 110S334 81 387 81S491 46 544 46S650 53 703 53S808 37 861 37V247H69Z" fill="var(--purple-fill)"/>
    <path d="M69 179C122 179 174 174 227 174S334 175 387 175S491 179 544 179S650 162 703 162S808 182 861 182V247H69Z" fill="var(--blue-fill)"/>
    <path d="M69 197C122 197 174 213 227 213S334 237 387 237S491 222 544 222S650 207 703 207S808 230 861 230V247H69Z" fill="var(--indigo-fill)"/>

    <g fill="none" stroke-width="2">
      <path d="M69 26C122 26 174 110 227 110S334 81 387 81S491 46 544 46S650 53 703 53S808 37 861 37" stroke="var(--purple)"/>
      <path d="M69 179C122 179 174 174 227 174S334 175 387 175S491 179 544 179S650 162 703 162S808 182 861 182" stroke="var(--blue)"/>
      <path d="M69 197C122 197 174 213 227 213S334 237 387 237S491 222 544 222S650 207 703 207S808 230 861 230" stroke="var(--indigo)"/>
    </g>
    <g fill="#fff" stroke-width="1.6">
      <g stroke="var(--purple)"><circle cx="69" cy="26" r="3.5"/><circle cx="227" cy="110" r="3.5"/><circle cx="387" cy="81" r="3.5"/><circle cx="544" cy="46" r="3.5"/><circle cx="703" cy="53" r="3.5"/><circle cx="861" cy="37" r="3.5"/></g>
      <g stroke="var(--blue)"><circle cx="69" cy="179" r="3.5"/><circle cx="227" cy="174" r="3.5"/><circle cx="387" cy="175" r="3.5"/><circle cx="544" cy="179" r="3.5"/><circle cx="703" cy="162" r="3.5"/><circle cx="861" cy="182" r="3.5"/></g>
      <g stroke="var(--indigo)"><circle cx="69" cy="197" r="3.5"/><circle cx="227" cy="213" r="3.5"/><circle cx="387" cy="237" r="3.5"/><circle cx="544" cy="222" r="3.5"/><circle cx="703" cy="207" r="3.5"/><circle cx="861" cy="230" r="3.5"/></g>
    </g>
  </svg>
</section>

<section class="card share"><div class="big">90%</div></section>
<section class="card platforms">
  <div class="legend"><i style="background:var(--cyan)"></i>Ixo <i style="background:var(--purple)"></i>Wendell <i style="background:var(--indigo)"></i>Andara</div>
</section>

</body>
</html>
```